Business Card Design

New business card design

Target Market(s)

Residential & Commercial Property Managers

Industry/Entity Type

Plumbing Services

Contact Information for Business Card

Name - Rowan Keddle, title - Director, Phone Number - 0431 286 517, email - rowan@tbk-plumbing.com.au, Company ABN - 73 215 904 386,

Font styles to use
Sans Serif

Colors
0054AA
0677BA
7BADD7
CADEEF
E8F1F8

```html
<!DOCTYPE html>
<html lang="en">
<head>
<meta charset="utf-8">
<title>TBK Plumbing Services – Business Card</title>
<link href="https://fonts.googleapis.com/css2?family=Montserrat:wght@400;500;700&display=swap" rel="stylesheet">
<style>
  :root {
    --backdrop: #d3d6d6;
    --card: #f1f1ef;
    --ink: #1b1d1f;
    --muted: #6f6a66;
    --brand-blue: #2aa8e0;
    --edge-blue: #0677ba;
  }
  * { box-sizing: border-box; margin: 0; padding: 0; }
  html, body { width: 1200px; height: 881px; overflow: hidden; }
  body {
    background: var(--backdrop);
    font-family: "Montserrat", sans-serif;
    color: var(--ink);
    position: relative;
  }
  .card {
    position: absolute;
    top: 292px;
    width: 520px;
    height: 297px;
    background: var(--card);
    border-bottom: 4px solid var(--edge-blue);
    box-shadow: 0 18px 40px rgba(0,0,0,0.18);
  }
  .card--contact { left: 50px; }
  .card--brand { left: 630px; }

  .wordmark { color: var(--ink); font-weight: 500; white-space: nowrap; }
  .wordmark__name { display: block; letter-spacing: 0.04em; }
  .wordmark__tagline { display: block; letter-spacing: 0.45em; text-transform: lowercase; }

  .card--contact .wordmark { position: absolute; left: 60px; top: 30px; }
  .card--contact .wordmark__name { font-size: 52px; line-height: 1; }
  .card--contact .wordmark__tagline { font-size: 10px; margin-top: 8px; }

  .card--brand .wordmark { position: absolute; left: 0; right: 0; top: 92px; text-align: center; }
  .card--brand .wordmark__name { font-size: 84px; line-height: 1; }
  .card--brand .wordmark__tagline { font-size: 13px; margin-top: 14px; }

  .person { position: absolute; left: 38px; top: 150px; padding-left: 14px; }
  .person::before {
    content: ""; position: absolute; left: 0; top: 2px;
    width: 7px; height: 40px; background: var(--brand-blue);
  }
  .person__name { font-size: 19px; font-weight: 700; color: var(--brand-blue); line-height: 1.1; }
  .person__title { font-size: 13px; font-weight: 400; margin-top: 2px; }

  .contact-list { position: absolute; left: 38px; top: 214px; list-style: none; font-size: 13px; }
  .contact-list li { display: flex; align-items: center; gap: 8px; line-height: 22px; }
  .contact-list svg { width: 12px; height: 12px; fill: var(--brand-blue); }

  .abn { position: absolute; right: 34px; bottom: 20px; font-size: 12px; }
</style>
</head>
<body>
  <section class="card card--contact">
    <div class="wordmark">
      <span class="wordmark__name">tbk</span>
      <span class="wordmark__tagline">plumbing services</span>
    </div>
    <div class="person">
      <p class="person__name">Rowan Keddle</p>
      <p class="person__title">Director</p>
    </div>
    <ul class="contact-list">
      <li>
        <svg viewBox="0 0 24 24" aria-hidden="true"><path d="M6.6 10.8a15.1 15.1 0 0 0 6.6 6.6l2.2-2.2a1 1 0 0 1 1-.25 11.4 11.4 0 0 0 3.6.57 1 1 0 0 1 1 1V20a1 1 0 0 1-1 1A17 17 0 0 1 3 4a1 1 0 0 1 1-1h3.5a1 1 0 0 1 1 1c0 1.25.2 2.45.57 3.57a1 1 0 0 1-.25 1z"/></svg>
        <span>0431 286 517</span>
      </li>
      <li>
        <svg viewBox="0 0 24 24" aria-hidden="true"><path d="M2 5h20v14H2zm2 2v.5l8 5 8-5V7zm0 2.8V17h16V9.8l-8 5z"/></svg>
        <span>rowan@tbk-plumbing.com.au</span>
      </li>
    </ul>
    <p class="abn">Company ABN - 73 215 904 386</p>
  </section>

  <section class="card card--brand">
    <div class="wordmark">
      <span class="wordmark__name">tbk</span>
      <span class="wordmark__tagline">plumbing services</span>
    </div>
  </section>
</body>
</html>
```